Open Harbor book needs a cover design

I need a front and back cover design that demonstrates a strong sense of possibility that trust can be repaired even if things look bleak. Repairing trust is difficult, but this book is full of wisdom, proven strategies, and doctoral research to help people strengthen relationships and improve trust. It can help any group: business, nonprofit, education, service. Showing diversity of groups and people is very important. For the cover title, there should be a play on words: "Open Harbor: Is it? Within Reach" should have the words "is it?" crossed out and the words "It IS! should be replaced there in a striking way. Perhaps in red ink. For publishing purposes, book will be titled Open Harbor: It IS Within Reach! Please see the attachment for an example. The book layout is approximately 260 pages.

A business self-help book, but the target is any person in a group that feels they have lost trust in each other. It can be just a normal person struggling in a volunteer group they are a part of, or a supervisor whose group is not working well together. It can be a leader who just wants their group to be stronger.

Business Management

• Allise - I believe is being used on the interior of the book for the title page and headings

• Show hope and possibility in the midst of difficulty. Must have a play on the words in the title "Open Harbor: Is it? Within Reach" with crossing out "is it?" with "It IS!" (see attached example) Must include the author's name: Marla Quentin, PhD Must include a smaller tagline: "Practical Steps to Move Teams Forward Again"
• Showing diverse people, or hands. Diverse kinds of groups - not just business. A colorful cover. Maybe show the complexity of trust when it is broken...broken pieces of trust that are then picked up and put together when people work together. Could show people (or images of hands) or other ways to show that it's a choice and it is possible to repair broken trust. I'd also like to convey a sense of a group - not just random people. That they have something at stake to work on repairing trust together and this book can help them.
• If images of people are used, just showing one gender or race is not okay. Nor just binary choices: like an image containing one man and one woman, or one white person and one person of color - otherwise it seems that the book on Open Harbor is about race or gender relations.

```html
<!DOCTYPE html>
<html lang="en">
<head>
<meta charset="utf-8">
<title>Open Harbor: It IS Within Reach! — Book Cover</title>
<link rel="stylesheet" href="https://fonts.googleapis.com/css2?family=Abril+Fatface&family=Cinzel:wght@400;500&display=swap">
<style>
  :root {
    --night: #0d1224;
    --deep-blue: #1a2350;
    --violet: #4a2a78;
    --magenta: #b0245c;
    --teal: #1f8fb5;
    --amber: #e8a11c;
    --ink-white: #ffffff;
    --strike-red: #d8321f;
    --piece-light: #f2f2f2;
    --piece-shade: #c9ccd4;
  }
  html, body {
    margin: 0;
    padding: 0;
    width: 762px;
    height: 1200px;
    overflow: hidden;
    background: var(--night);
  }
  .cover {
    position: relative;
    width: 762px;
    height: 1200px;
    overflow: hidden;
    background: var(--night);
    color: var(--ink-white);
  }
  .cover-art {
    position: absolute;
    inset: 0;
    background:
      radial-gradient(ellipse 260px 320px at 420px 380px, rgba(74,42,120,0.75), transparent 70%),
      radial-gradient(ellipse 180px 140px at 300px 520px, rgba(176,36,92,0.45), transparent 70%),
      radial-gradient(ellipse 160px 120px at 560px 330px, rgba(31,143,181,0.45), transparent 70%),
      radial-gradient(ellipse 120px 90px at 620px 600px, rgba(232,161,28,0.30), transparent 70%),
      radial-gradient(ellipse 420px 500px at 380px 420px, rgba(26,35,80,0.9), transparent 75%),
      var(--night);
  }
  .author {
    position: absolute;
    top: 46px;
    left: 0;
    width: 762px;
    margin: 0;
    text-align: center;
    font-family: "Cinzel", serif;
    font-weight: 400;
    font-size: 31px;
    letter-spacing: 8px;
    color: var(--ink-white);
  }
  .title {
    position: absolute;
    top: 0;
    left: 0;
    width: 762px;
    height: 700px;
  }
  .title text {
    font-family: "Abril Fatface", serif;
    fill: var(--ink-white);
  }
  .tagline {
    position: absolute;
    top: 630px;
    left: 0;
    width: 762px;
    margin: 0;
    text-align: center;
    font-family: "Cinzel", serif;
    font-weight: 400;
    font-size: 19px;
    line-height: 26px;
    letter-spacing: 0.5px;
    text-transform: uppercase;
    color: var(--ink-white);
  }
  .group-illustration {
    position: absolute;
    top: 772px;
    left: 184px;
    width: 394px;
    height: 296px;
    background: linear-gradient(160deg, var(--piece-light), var(--piece-shade));
  }
  .publisher {
    position: absolute;
    top: 1126px;
    left: 620px;
    display: flex;
    align-items: center;
    gap: 7px;
    font-family: "Cinzel", serif;
    font-weight: 500;
    font-size: 13px;
    line-height: 15px;
    color: var(--ink-white);
  }
  .publisher-mark {
    width: 20px;
    height: 20px;
    background: var(--ink-white);
  }
</style>
</head>
<body>
  <main class="cover">
    <div class="cover-art" role="img" aria-label="Abstract swirling ribbons and shards of colour in violet, magenta, teal and amber against a dark night-blue background"></div>

    <p class="author">MARLA QUENTIN, PHD</p>

    <svg class="title" viewBox="0 0 762 700" aria-label="Open Harbor: It IS Within Reach!">
      <text x="194" y="304" font-size="212" textLength="377" lengthAdjust="spacingAndGlyphs">OPEN</text>
      <text x="194" y="463" font-size="212" textLength="380" lengthAdjust="spacingAndGlyphs">HARBOR</text>
      <text x="194" y="577" font-size="34" textLength="77" lengthAdjust="spacingAndGlyphs">IT IS</text>
      <text x="194" y="622" font-size="46" textLength="77" lengthAdjust="spacingAndGlyphs">IS IT?</text>
      <line x1="190" y1="614" x2="276" y2="596" stroke="var(--strike-red)" stroke-width="6" stroke-linecap="round"/>
      <text x="283" y="624" font-size="104" textLength="295" lengthAdjust="spacingAndGlyphs">WITHIN REACH</text>
    </svg>

    <p class="tagline">Practical Steps to<br>Move Teams Forward Again</p>

    <div class="group-illustration" role="img" aria-label="White jigsaw puzzle pieces fitting together, each holding black silhouettes of diverse people in groups — sitting, working and high-fiving"></div>

    <div class="publisher">
      <span class="publisher-mark"></span>
      <span>QUAYSIDE<br>PRESS</span>
    </div>
  </main>
</body>
</html>
```